Velmora TV mobile app tiles/images.

I want to redo the images currently shown on our Orbit and Quince App Store download pages. Attached is an example of a design that I like. And beneath that are our logos. The 2 that say Velmora are our company logo and the VTV logo is specifically the logo for our app.

Please prioritize the Live TV feature and note that the preferred content to focus on has been uploaded.

Target Market(s)

African and African Americans

Industry/Entity Type

Movie and TV industry

Colors
FFC000
F8CF3A
FAE287
FDF2CF
FEFAEE

Requirements
Must have
• Black models and actors in the artwork.
Should not have
• Any explicit images or words. I will provide contact titles that can be used.

```html
<!DOCTYPE html>
<html lang="en">
<head>
<meta charset="utf-8">
<title>Velmora TV – App Screens</title>
<link href="https://fonts.googleapis.com/css2?family=Barlow:wght@400;700;800&family=Roboto:wght@300;400;500&family=Montserrat:wght@400&display=swap" rel="stylesheet">
<style>
:root{
  --gold:#FFC000;
  --gold-2:#F8CF3A;
  --gold-3:#FAE287;
  --gold-4:#FDF2CF;
  --cream:#FEFAEE;
  --brand-gold:#c9a23a;
  --ink:#0b0b0b;
  --grey:#555;
  --screen:#1d2030;
  --screen-2:#272b3d;
  --ring:#2a1a10;
}
*{box-sizing:border-box;margin:0;padding:0}
html,body{width:1015px;height:1200px;overflow:hidden;background:#fff}
body{position:relative;font-family:'Roboto',sans-serif;color:var(--ink)}
.page-title{position:absolute;top:28px;left:0;width:1015px;text-align:center;font-family:'Montserrat',sans-serif;font-weight:400;font-size:29px;letter-spacing:14px}
.tile{position:absolute;width:257px;overflow:hidden;box-shadow:0 6px 10px rgba(0,0,0,.12);
  background:linear-gradient(155deg,var(--cream) 0%,var(--gold-3) 30%,var(--gold-2) 48%,var(--gold-4) 62%,var(--gold) 80%,var(--gold-4) 100%)}
.row-1{top:81px;height:508px}
.row-2{top:656px;height:512px}
.col-1{left:71px}.col-2{left:384px}.col-3{left:694px}
.tile-deco{position:absolute;inset:0}
.brand{position:absolute;display:flex;align-items:center;gap:7px;font-family:'Barlow',sans-serif;font-weight:700;font-size:13px;color:var(--brand-gold)}
.brand .divider{width:1px;height:18px;background:var(--brand-gold)}
.row-1 .brand{top:16px;left:0;width:100%;justify-content:center}
.row-2 .brand{top:22px;left:12px}
.heading{position:absolute;font-family:'Barlow',sans-serif;font-weight:800;font-size:21px;line-height:20px}
.sub{position:absolute;font-size:8.6px;line-height:11px;color:var(--grey);font-weight:300}
.row-1 .heading,.row-1 .sub{left:0;width:100%;text-align:center}
.row-2 .heading,.row-2 .sub{right:9px;text-align:right}
.phone{position:absolute;background:#2b2e38;border-radius:16px;border:2px solid #4a4d57;padding:12px 3px 14px}
.phone .screen{width:100%;height:100%;background:var(--screen);overflow:hidden;position:relative;color:#fff}
.appbar{height:17px;display:flex;align-items:center;justify-content:center;font-size:5.5px;letter-spacing:.3px;position:relative}
.appbar .menu{position:absolute;left:6px;top:6px;width:6px;height:4px;border-top:1px solid #fff;border-bottom:1px solid #fff}
.appbar .avatar{position:absolute;right:4px;top:3px;width:10px;height:10px;border-radius:50%;background:#d8a56f}
.tabbar{position:absolute;bottom:0;left:0;right:0;height:16px;display:flex;justify-content:space-around;align-items:center;background:var(--screen)}
.tabbar i{width:5px;height:5px;border:1px solid #ccc;border-radius:1px;display:block}
.tabbar i.on{border-color:var(--brand-gold)}
.ring{position:absolute;width:18px;height:18px;border:2.5px solid var(--ink);border-radius:50%}
.media{position:absolute;box-shadow:0 3px 8px rgba(0,0,0,.35)}
/* login */
.login-mark{position:absolute;top:68px;width:100%;text-align:center;font-family:'Barlow',sans-serif;font-weight:700;font-size:17px;color:var(--brand-gold)}
.login-form{position:absolute;left:5px;right:5px;top:126px;font-size:4.4px;color:#bbb}
.login-form h4{font-size:8px;color:#fff;font-weight:500;margin-bottom:10px}
.field{border-bottom:1px solid #777;height:18px;margin-bottom:8px}
.btn{background:#b3932d;color:#fff;text-align:center;height:13px;line-height:13px;font-size:5px;margin-top:4px}
.link{text-align:center;margin-top:7px}
.link.gold{color:var(--brand-gold);font-size:5px}
/* lists */
.row-item{display:flex;gap:5px;padding:3px 4px;height:38px}
.thumb{width:60px;height:30px;flex:none;display:flex;align-items:center;justify-content:center;font-size:5px;font-weight:500;color:#fff}
.row-item .txt{font-size:4.3px;line-height:5.5px;color:#aaa}
.row-item .txt b{display:block;color:#fff;font-weight:400;margin-bottom:2px}
.mag-item{display:flex;gap:4px;padding:2px 4px;height:27px;border-bottom:1px solid #2c3044}
.mag-item .thumb{width:19px;height:19px}
.mag-item .txt{font-size:3.8px;line-height:5px;color:#fff}
.mag-item .txt span{display:block;color:#aaa}
.section-head{display:flex;justify-content:space-between;font-size:4.5px;padding:4px;color:var(--brand-gold)}
.section-head span:last-child{color:#ddd}
/* tablet & grid */
.tablet{position:absolute;background:#2b2e38;border-radius:9px;padding:4px 10px}
.chips{display:flex;gap:2px;padding:2px 4px}
.chips span{font-size:3px;padding:1px 4px;background:#333850;color:#ccc}
.chips span.on{background:#b3932d;color:#fff}
.grid{display:grid;gap:3px;padding:3px 4px}
.grid div{border-radius:1px}
</style>
</head>
<body>

<h1 class="page-title">APP SCREENS</h1>

<!-- Tile 1: login -->
<section class="tile row-1 col-1">
  <svg class="tile-deco" viewBox="0 0 257 508" preserveAspectRatio="none" role="img" aria-label="Faceted golden crystal background">
    <polygon points="0,0 257,0 257,78 190,62 125,40 70,58 0,72" fill="#0b0b0b"/>
    <path d="M35,508 A95,95 0 0 1 225,508" fill="none" stroke="var(--ring)" stroke-width="8"/>
  </svg>
  <div class="brand"><span>VTV</span><span class="divider"></span><span>Velmora</span></div>
  <h2 class="heading" style="top:79px">Login &amp; Enjoy</h2>
  <p class="sub" style="top:105px">Access your favorite, Movies &amp; Entertainment<br>with eassy login anytime.</p>
  <div class="phone" style="left:60px;top:143px;width:135px;height:293px">
    <div class="screen">
      <div class="login-mark">VTV</div>
      <div class="login-form">
        <h4>LOGIN</h4>
        <div class="field">Email address</div>
        <div class="field">Password</div>
        <div class="btn">Login</div>
        <div class="link gold">Register</div>
        <div class="link">Forgot password? Reset here</div>
      </div>
    </div>
  </div>
  <span class="ring" style="left:233px;top:443px"></span>
  <span class="ring" style="left:73px;top:488px"></span>
</section>

<!-- Tile 2: live TV -->
<section class="tile row-1 col-2">
  <svg class="tile-deco" viewBox="0 0 257 508" preserveAspectRatio="none" role="img" aria-label="Faceted golden crystal background">
    <polygon points="0,0 257,0 257,78 190,62 125,40 70,58 0,72" fill="#0b0b0b"/>
    <path d="M35,508 A95,95 0 0 1 225,508" fill="none" stroke="var(--ring)" stroke-width="8"/>
  </svg>
  <div class="brand"><span>VTV</span><span class="divider"></span><span>Velmora</span></div>
  <h2 class="heading" style="top:79px">Watch Live TV</h2>
  <p class="sub" style="top:102px">Never miss any show or news with Velmora app.<br>Get access to Live TV anytime.</p>
  <div class="phone" style="left:60px;top:143px;width:135px;height:293px">
    <div class="screen">
      <div class="appbar"><span class="menu"></span>LIVE TV<span class="avatar"></span></div>
      <div role="img" aria-label="Live news broadcast with studio guests" style="height:72px;background:linear-gradient(135deg,#8a94a6,#c9ced8 50%,#6b7384)"></div>
      <div style="height:6px;background:var(--gold-2)"></div>
      <div style="padding-top:8px">
        <div class="row-item"><div class="thumb" style="background:linear-gradient(135deg,#caa03a,#e8c55a)">Sahel News</div><div class="txt"><b>Sahel News</b>Daily news from across the continent</div></div>
        <div class="row-item"><div class="thumb" style="background:#123a7a">Northline</div><div class="txt"><b>Northline News</b>National and current affairs coverage</div></div>
        <div class="row-item"><div class="thumb" style="background:#c4171b">Meridian</div><div class="txt"><b>Meridian News Network</b>A worldwide pay news channel</div></div>
        <div class="row-item"><div class="thumb" style="background:#8e1418">Crown World</div><div class="txt"><b>Crown World News</b>International news in English</div></div>
      </div>
      <div class="tabbar"><i class="on"></i><i></i><i></i><i></i><i></i><i></i></div>
    </div>
  </div>
  <span class="ring" style="left:233px;top:443px"></span>
  <span class="ring" style="left:73px;top:488px"></span>
</section>

<!-- Tile 3: magazine -->
<section class="tile row-1 col-3">
  <svg class="tile-deco" viewBox="0 0 257 508" preserveAspectRatio="none" role="img" aria-label="Faceted golden crystal background">
    <polygon points="0,0 257,0 257,78 190,62 125,40 70,58 0,72" fill="#0b0b0b"/>
    <path d="M35,508 A95,95 0 0 1 225,508" fill="none" stroke="var(--ring)" stroke-width="8"/>
  </svg>
  <div class="brand"><span>VTV</span><span class="divider"></span><span>Velmora</span></div>
  <h2 class="heading" style="top:79px">Magazine for all<br>Interests</h2>
  <p class="sub" style="top:120px">Choose &amp; Save your Reading Experience</p>
  <div class="phone" style="left:60px;top:143px;width:135px;height:293px">
    <div class="screen">
      <div class="appbar"><span class="menu"></span>MAGAZINE<span class="avatar"></span></div>
      <div role="img" aria-label="Marathon runner celebrating with a flag" style="margin:4px 8px 0;height:78px;background:linear-gradient(160deg,#b8202a,#2a2a2a 45%,#2d6b3a);position:relative">
        <div style="position:absolute;left:4px;bottom:4px;font-size:4.3px;line-height:5.5px">Kenyan runner Kamau Oduya<br>wins city marathon and sets ...<br><span style="color:#ccc">2022-09-26 · Kojo Mensar</span></div>
      </div>
      <div class="section-head"><span>Industry Pulse</span><span>View all</span></div>
      <div class="mag-item"><div class="thumb" style="background:#c0392b"></div><div class="txt">Ama Serwaa Puts On A Live Show At Unity Sound Festival<span>2022-09-26 00:00:00</span></div></div>
      <div class="mag-item"><div class="thumb" style="background:#5a2a6a"></div><div class="txt">Coastline Fest Announces Dates For 2023<span>2022-09-26 00:00:00</span></div></div>
      <div class="mag-item"><div class="thumb" style="background:#3a4a6a"></div><div class="txt">Dela Owusu Speaks Out On Recent Staff Reports<span>2022-09-27 00:00:00</span></div></div>
      <div class="mag-item"><div class="thumb" style="background:#2a66b0"></div><div class="txt">Unity Sound Campaign Raises $2.4 Billion For Schools<span>2022-09-25 00:00:00</span></div></div>
      <div class="mag-item"><div class="thumb" style="background:#7a5a3a"></div><div class="txt">Tobi Rankin Praises New Watch Collection</div></div>
      <div class="tabbar"><i></i><i></i><i></i><i></i><i class="on"></i><i></i></div>
    </div>
  </div>
  <span class="ring" style="left:233px;top:443px"></span>
  <span class="ring" style="left:73px;top:488px"></span>
</section>

<!-- Tile 4: the gold -->
<section class="tile row-2 col-1">
  <svg class="tile-deco" viewBox="0 0 257 512" preserveAspectRatio="none" role="img" aria-label="Faceted golden crystal background">
    <polygon points="0,0 120,0 105,45 55,70 25,130 0,135" fill="#0b0b0b"/>
    <path d="M-20,512 A120,120 0 0 1 200,512" fill="none" stroke="var(--ring)" stroke-width="8"/>
  </svg>
  <div class="brand"><span>VTV</span><span class="divider"></span><span>Velmora</span></div>
  <h2 class="heading" style="top:26px">VELMORA<br>The Gold</h2>
  <p class="sub" style="top:72px">Cut the cable cord &amp; enjoy.<br>We aim to be the one stop solution<br>for all of your media entertainment.</p>
  <div class="media" role="img" aria-label="Drama poster: Golden Hour, women posed around a white throne" style="left:108px;top:120px;width:108px;height:183px;background:linear-gradient(160deg,#f6b52e,#e98e2a 60%,#c9663a)"></div>
  <div class="media" role="img" aria-label="Action poster: Shadow Child, masked fighter" style="left:23px;top:194px;width:107px;height:183px;background:linear-gradient(160deg,#c9a070,#7a4a30 55%,#3a2218)"></div>
  <div class="media" role="img" aria-label="Comedy poster: Home with Uncle Bayo, family portrait" style="left:128px;top:324px;width:108px;height:183px;background:linear-gradient(160deg,#2a8ad0,#1a4a8a 60%,#0f2a5a)"></div>
  <span class="ring" style="left:75px;top:480px"></span>
</section>

<!-- Tile 5: entertainment -->
<section class="tile row-2 col-2">
  <svg class="tile-deco" viewBox="0 0 257 512" preserveAspectRatio="none" role="img" aria-label="Faceted golden crystal background">
    <polygon points="0,0 120,0 105,45 55,70 25,130 0,135" fill="#0b0b0b"/>
    <path d="M-20,512 A120,120 0 0 1 200,512" fill="none" stroke="var(--ring)" stroke-width="8"/>
  </svg>
  <div class="brand"><span>VTV</span><span class="divider"></span><span>Velmora</span></div>
  <h2 class="heading" style="top:28px">Your Real<br>Entertainment</h2>
  <p class="sub" style="top:72px">Your Entertainment<br>at your fingertips, at your terms,<br>anytime, only at VTV</p>
  <div class="media" role="img" aria-label="Drama poster: Quiet Secrets, woman with covered eyes" style="left:23px;top:163px;width:106px;height:180px;background:linear-gradient(160deg,#3a2a18,#b48a3a 45%,#1a120a)"></div>
  <div class="media" role="img" aria-label="Action poster: Ring Warrior 2, fighter mid kick" style="left:126px;top:119px;width:107px;height:180px;background:linear-gradient(160deg,#6a7078,#b8bcc0 55%,#4a4e54)"></div>
  <div class="media" role="img" aria-label="Thriller poster: The Deacon, dark red figure" style="left:106px;top:306px;width:107px;height:180px;background:linear-gradient(160deg,#5a1a14,#3a2a20 55%,#1a1410)"></div>
  <span class="ring" style="left:75px;top:478px"></span>
</section>

<!-- Tile 6: movies anytime -->
<section class="tile row-2 col-3">
  <svg class="tile-deco" viewBox="0 0 257 512" preserveAspectRatio="none" role="img" aria-label="Faceted golden crystal background">
    <polygon points="0,0 120,0 105,45 55,70 25,130 0,135" fill="#0b0b0b"/>
    <path d="M-20,512 A120,120 0 0 1 200,512" fill="none" stroke="var(--ring)" stroke-width="8"/>
  </svg>
  <div class="brand"><span>VTV</span><span class="divider"></span><span>Velmora</span></div>
  <h2 class="heading" style="top:28px">Watch<br>Movies Anytime</h2>
  <p class="sub" style="top:76px">Anytime Access your favorite movie<br>on any device, download &amp; save it<br>with complete history.</p>
  <div class="tablet" style="left:21px;top:147px;width:214px;height:143px">
    <div class="screen" style="background:var(--screen);height:100%;color:#fff;overflow:hidden">
      <div class="appbar" style="height:10px;font-size:3.5px">TV SHOWS</div>
      <div class="chips"><span class="on">All</span><span>African</span><span>Comedy</span><span>Drama</span><span>Ghana</span><span>West African</span></div>
      <div class="grid" style="grid-template-columns:repeat(3,1fr);grid-auto-rows:24px">
        <div style="background:#8a3a9a"></div><div style="background:#c9a03a"></div><div style="background:#3a6aa8"></div>
        <div style="background:#d83a7a"></div><div style="background:#f2c218"></div><div style="background:#e8a02a"></div>
        <div style="background:#5a6ab8"></div><div style="background:#3a3a4a"></div><div style="background:#7a4a3a"></div>
      </div>
    </div>
  </div>
  <div class="phone" style="left:80px;top:240px;width:96px;height:208px;border-radius:12px;padding:9px 2px 10px">
    <div class="screen">
      <div class="appbar" style="height:12px;font-size:4px">MOVIES<span class="avatar" style="width:7px;height:7px"></span></div>
      <div class="chips"><span class="on">All</span><span>Documentary</span><span>Sport</span></div>
      <div class="grid" style="grid-template-columns:repeat(3,1fr);grid-auto-rows:28px;gap:2px">
        <div style="background:#2a7ac8"></div><div style="background:#b82a2a"></div><div style="background:#c84a3a"></div>
        <div style="background:#5a3a2a"></div><div style="background:#3a4a6a"></div><div style="background:#6a5a4a"></div>
        <div style="background:#8a2a2a"></div><div style="background:#2a2a2a"></div><div style="background:#a8302a"></div>
        <div style="background:#9a6a4a"></div><div style="background:#6a4a3a"></div><div style="background:#3a6a3a"></div>
      </div>
      <div class="tabbar" style="height:12px"><i></i><i></i><i class="on"></i><i></i><i></i><i></i></div>
    </div>
  </div>
  <span class="ring" style="left:75px;top:478px"></span>
</section>

</body>
</html>
```